Web Developer Needs a Business Card Design

I need a personal business card design that represents me as a web developer for potential employers. I would like the background to be a dark color on the front for contrast with my logo and name. The back will have all my information along with a smaller version of the logo. I want something with a modern look and feel, not too conservative. This will be used for potential employers and freelance work.

Industry/Entity Type

Business

Contact Information for Business Card

Front should have my logo and name. The back should have all my personal information which would include: name: Tom Varulek, phone: 570-614-3098, email: tomvarulek@quillbox.net, website url: www.tomvarulek.net, logo, web developer.

Font styles to use
Sans Serif

Requirements
Must have
• Must include my logo. The color palette base color will be the logo color.

```html
<!DOCTYPE html>
<html lang="en">
<head>
<meta charset="utf-8">
<title>Tom Varulek – Business Card</title>
<link rel="stylesheet" href="https://fonts.googleapis.com/css2?family=Open+Sans:wght@400;600&display=swap">
<style>
  :root {
    --teal: #7ccbbb;
    --teal-dark: #5fb3a3;
    --ink: #050505;
    --white: #ffffff;
    --backdrop: #e9e6e1;
  }
  * { box-sizing: border-box; margin: 0; padding: 0; }
  html, body { width: 1200px; height: 892px; overflow: hidden; }
  body {
    background: var(--backdrop);
    font-family: "Open Sans", Arial, sans-serif;
    display: flex;
    align-items: center;
    justify-content: center;
    gap: 40px;
  }
  .card {
    position: relative;
    width: 540px;
    height: 309px;
    border-radius: 18px;
    overflow: hidden;
    box-shadow: 0 10px 28px rgba(0,0,0,.25);
  }
  .card-bands { position: absolute; inset: 0; width: 100%; height: 100%; }
  .card-content {
    position: absolute;
    inset: 0;
    display: flex;
    flex-direction: column;
    align-items: center;
  }
  .mark-ring {
    border: 9px solid var(--teal);
    border-radius: 50%;
    background: var(--ink);
  }
  /* back side */
  .card--back .card-content { padding-top: 34px; }
  .card--back .mark-ring { width: 96px; height: 96px; }
  .details { margin-top: 16px; text-align: left; }
  .name { color: var(--teal); font-size: 30px; font-weight: 400; line-height: 1.05; letter-spacing: .5px; }
  .role { color: var(--white); font-size: 17px; line-height: 1.2; margin-bottom: 10px; }
  .contact { list-style: none; color: var(--white); font-size: 13.5px; line-height: 1.45; }
  /* front side */
  .card--front .card-content {
    flex-direction: row;
    justify-content: center;
    gap: 30px;
  }
  .card--front .front-name { color: var(--white); font-size: 34px; font-weight: 400; letter-spacing: .5px; }
  .card--front .mark-ring { width: 150px; height: 150px; border-width: 12px; }
</style>
</head>
<body>

  <section class="card card--back" aria-label="Card back">
    <svg class="card-bands" viewBox="0 0 540 309" preserveAspectRatio="none" aria-hidden="true">
      <defs>
        <linearGradient id="tealBack" x1="0" y1="0" x2="1" y2="1">
          <stop offset="0" stop-color="var(--teal)"/>
          <stop offset="1" stop-color="var(--teal-dark)"/>
        </linearGradient>
      </defs>
      <rect width="540" height="309" fill="url(#tealBack)"/>
      <path d="M72,0 H468 Q503,154 468,309 H72 Q37,154 72,0 Z" fill="var(--ink)"/>
      <path d="M87,0 Q52,154 87,309" fill="none" stroke="var(--teal)" stroke-width="4"/>
      <path d="M453,0 Q488,154 453,309" fill="none" stroke="var(--teal)" stroke-width="4"/>
    </svg>
    <div class="card-content">
      <div class="mark-ring" role="img" aria-label="Personal mark"></div>
      <div class="details">
        <h1 class="name">Tom Varulek</h1>
        <p class="role">web developer</p>
        <ul class="contact">
          <li>570-614-3098</li>
          <li>www.tomvarulek.net</li>
          <li>tomvarulek@quillbox.net</li>
        </ul>
      </div>
    </div>
  </section>

  <section class="card card--front" aria-label="Card front">
    <svg class="card-bands" viewBox="0 0 540 309" preserveAspectRatio="none" aria-hidden="true">
      <defs>
        <linearGradient id="tealFront" x1="0" y1="0" x2="1" y2="1">
          <stop offset="0" stop-color="var(--teal)"/>
          <stop offset="1" stop-color="var(--teal-dark)"/>
        </linearGradient>
      </defs>
      <rect width="540" height="309" fill="url(#tealFront)"/>
      <path d="M72,0 H468 Q503,154 468,309 H72 Q37,154 72,0 Z" fill="var(--ink)"/>
      <path d="M87,0 Q52,154 87,309" fill="none" stroke="var(--teal)" stroke-width="4"/>
      <path d="M453,0 Q488,154 453,309" fill="none" stroke="var(--teal)" stroke-width="4"/>
    </svg>
    <div class="card-content">
      <h2 class="front-name">Tom Varulek</h2>
      <div class="mark-ring" role="img" aria-label="Personal mark"></div>
    </div>
  </section>

</body>
</html>
```